Corlani Vaginal Suppositories eCommerce Website Design

We are designing an ecommerce website for a new company and product. The product is vaginal moisturizer suppositories. We are going to develop this site on Shopify so you can add in any featured you have knowledge of in Shopify.

We are purposefully not adding any images to allow you to create something with your style. A similar product is tandelivy.com. We would like a site similar to this in style, but obviously different not to look the same. It is a product for women so it needs to be a very feminine theme. We have had designers use thier own illustrations in previous designs that looked great, or stock images that don't look "stock" would be good. We would like the product section to look like a normal product section on Shopify, specified in the link below. The rest of the site with the featues and benefits and ingredients can be displayed creatively with images, illustrations, or product placement interspersed. Use any high quality images you have access to and we will purchase if necessary.

Use icons and symbols to represent the different benefits and ingredients.

Pay no attention to colors in the wireframe. The only defitinte color is the logo.

I put a picture of the actual suppositories so we would like to intersperse that (an individual one, not inside the package) in a few places. You can use it in the directions section for sure.

Video about wireframe: https://files.brovantic.net/file/d/9Kq2mRtzPw4LxVb7Hn3JcYd5FgS8aZeUo/view?usp=share

https://slides.brovantic.net/deck/d/7Tm3WqLpZx8NcRv2Bk6YhJs4DfG5aQeUi/edit?usp=share&uid=408213957260318846115&mode=true&full=true

Target Market(s)

Women

Industry/Entity Type

Healthcare

Number of Pages Required

1 page

Requirements
Must have
• I added a "wireframe" in the description
Nice to have
Should not have

```html
<!DOCTYPE html>
<html lang="en">
<head>
<meta charset="utf-8">
<title>Corlani — Vaginal Moisturizer Suppositories</title>
<link rel="stylesheet" href="https://fonts.googleapis.com/css2?family=Libre+Baskerville&family=Inter:wght@400;500;600&display=swap">
<style>
  :root {
    --topbar: #ebc4c9;
    --topbar-text: #5a3d42;
    --brand: #d4317e;
    --nav-text: #3b3336;
    --nav-active: #d2463f;
    --hero-pink: #ecd6d8;
    --hero-soft: #f7eeee;
    --ink: #3a3033;
    --button: #3a2d2d;
    --accent: #c0574b;
    --orange: #f2874a;
    --tab-pink: #f8e3e3;
    --tab-soft: #faf2f2;
    --card: #f8f6f6;
    --line: #e6dcdd;
    --pill: #f6f3f3;
    --white: #ffffff;
  }
  * { box-sizing: border-box; margin: 0; padding: 0; }
  html, body { width: 1200px; height: 800px; overflow: hidden; background: var(--white); }
  body { position: relative; font-family: "Inter", Arial, sans-serif; color: var(--ink); }

  .topbar { position: absolute; left: 0; top: 0; width: 1200px; height: 34px; background: var(--topbar);
    font-size: 10.5px; letter-spacing: .04em; color: var(--topbar-text); text-transform: uppercase; }
  .topbar span { position: absolute; top: 11px; line-height: 13px; }
  .topbar .close { right: 12px; top: 12px; width: 9px; height: 9px; border: 1.3px solid var(--topbar-text); }

  .header { position: absolute; left: 0; top: 34px; width: 1200px; height: 60px; }
  .logo { position: absolute; left: 28px; top: 16px; display: flex; align-items: center; gap: 7px;
    font-weight: 600; font-size: 24px; line-height: 28px; color: var(--brand); }
  .logo i { display: block; width: 12px; height: 12px; border-radius: 50%; background: var(--brand); }
  .nav { position: absolute; left: 372px; top: 24px; display: flex; gap: 30px; font-size: 10.5px; line-height: 13px; letter-spacing: .06em; color: var(--nav-text); }
  .nav a { text-decoration: none; color: inherit; }
  .nav a.active { color: var(--nav-active); }
  .tools { position: absolute; left: 1030px; top: 0; width: 170px; height: 60px; }
  .search-pill { position: absolute; left: 12px; top: 15px; width: 60px; height: 30px; border-radius: 15px; background: var(--pill); }
  .menu-dot { position: absolute; left: 124px; top: 15px; width: 31px; height: 31px; border-radius: 50%; background: var(--orange); }

  .hero-main { position: absolute; left: 2px; top: 95px; width: 594px; height: 353px; border-radius: 10px; background: var(--hero-pink); overflow: hidden; }
  .hero-art { position: absolute; left: 40px; top: 25px; width: 230px; height: 290px; border-radius: 45% 55% 40% 60% / 30% 40% 60% 70%;
    background: radial-gradient(circle at 55% 20%, #f2b48e 0 18%, transparent 30%), linear-gradient(160deg, #f6d2c8, #bfe3e0 55%, #f1c8c8); opacity: .85; }
  .hero-copy { position: absolute; left: 210px; top: 100px; width: 370px; text-align: center; }
  .hero-copy h1 { font-family: "Libre Baskerville", Georgia, serif; font-weight: 400; font-size: 32px; line-height: 40px; color: #3c3235; }
  .hero-copy p { margin-top: 14px; font-family: "Libre Baskerville", Georgia, serif; font-size: 11.5px; line-height: 16px; color: #4a3f42; }
  .btn { display: inline-block; margin-top: 20px; padding: 0 24px; height: 37px; line-height: 37px; border-radius: 19px;
    background: var(--button); color: #f5ecec; font-size: 10px; letter-spacing: .05em; text-transform: uppercase; }

  .hero-offer { position: absolute; left: 603px; top: 95px; width: 278px; height: 353px; border-radius: 10px; background: var(--hero-soft); text-align: center; }
  .hero-offer .lead { position: absolute; top: 84px; width: 100%; font-family: "Libre Baskerville", Georgia, serif; font-size: 16px; line-height: 24px; }
  .hero-offer .pct { position: absolute; top: 172px; width: 100%; font-family: "Libre Baskerville", Georgia, serif; font-size: 18px; line-height: 29px; color: var(--accent); }
  .hero-offer .rule { position: absolute; top: 240px; left: 87px; width: 104px; height: 1.5px; background: var(--accent); }
  .hero-offer .tag { position: absolute; top: 271px; width: 100%; font-size: 12px; letter-spacing: .03em; }

  .hero-photo { position: absolute; left: 888px; top: 95px; width: 310px; height: 353px; border-radius: 10px; background: var(--white); overflow: hidden; }
  .hero-photo .portrait { position: absolute; left: 0; top: 10px; width: 310px; height: 343px; border-radius: 50% 50% 0 0 / 55% 55% 0 0;
    background: radial-gradient(circle at 55% 45%, #f0d7c7 0 30%, #ecdedd 60%, #f4eeee); }
  .badge { position: absolute; left: 6px; top: 312px; padding: 7px 10px; border-radius: 14px; background: #f7f1ef; font-size: 18px; line-height: 20px; color: #4a3f42; }
  .heart { position: absolute; right: 4px; top: 318px; width: 26px; height: 26px; border-radius: 50%; background: var(--white); }

  .tabs { position: absolute; left: 3px; top: 460px; display: flex; gap: 6px; }
  .tab { width: 194px; height: 42px; border-radius: 8px; background: var(--tab-soft); display: flex; align-items: center; justify-content: center;
    font-size: 13.5px; color: #3c3436; text-transform: uppercase; }
  .tab.highlight { background: var(--tab-pink); }

  .divider { position: absolute; left: 0; top: 539px; width: 1200px; height: 1px; background: var(--line); }

  .products { position: absolute; left: 2px; top: 551px; display: flex; gap: 8px; }
  .card { position: relative; width: 233px; height: 260px; border-radius: 8px; background: var(--card); text-align: center; }
  .card .shot { position: absolute; left: 56px; top: 30px; width: 120px; height: 115px; border-radius: 8px;
    background: linear-gradient(180deg, #f1e6e3, #e4d3cf); }
  .card h3 { position: absolute; top: 164px; width: 100%; font-family: "Libre Baskerville", Georgia, serif; font-weight: 400; font-size: 15px; line-height: 21px; color: #3a3033; }
  .card a { position: absolute; top: 219px; left: 0; width: 100%; font-size: 9.5px; letter-spacing: .04em; color: var(--accent); text-decoration: none; text-transform: uppercase; }
</style>
</head>
<body>
  <div class="topbar">
    <span style="left:380px">Free shipping over $40</span>
    <span style="left:532px">Shop suppositories ▾</span>
    <span style="left:737px">Discreet delivery ▾</span>
    <span class="close"></span>
  </div>

  <header class="header">
    <div class="logo"><i></i>Corlani</div>
    <nav class="nav">
      <a class="active" href="#">SHOP</a><a href="#">RELIEF</a><a href="#">BENEFITS</a><a href="#">INGREDIENTS</a><a href="#">HOW TO USE</a><a href="#">FAQ</a><a href="#">REVIEWS</a>
    </nav>
    <div class="tools">
      <div class="search-pill"></div>
      <svg style="position:absolute;left:24px;top:24px" width="12" height="12" viewBox="0 0 12 12" fill="none" stroke="#3b3336" stroke-width="1.4"><circle cx="5" cy="5" r="3.6"/><path d="M8 8l3 3"/></svg>
      <svg style="position:absolute;left:52px;top:24px" width="8" height="12" viewBox="0 0 8 12" fill="none" stroke="#3b3336" stroke-width="1.4"><path d="M2 1l4 5-4 5"/></svg>
      <svg style="position:absolute;left:96px;top:22px" width="16" height="16" viewBox="0 0 16 16" fill="none" stroke="#3b3336" stroke-width="1.3"><path d="M1 2h2.5l1.8 8h7.5l1.5-6H4.2"/><circle cx="6" cy="13.5" r="1"/><circle cx="12" cy="13.5" r="1"/></svg>
      <div class="menu-dot"></div>
      <svg style="position:absolute;left:133px;top:25px" width="13" height="11" viewBox="0 0 13 11" fill="none" stroke="#fff" stroke-width="1.3"><rect x="1" y="1" width="11" height="9" rx="1.5"/><path d="M3 4.5h7M3 6.5h7"/></svg>
    </div>
  </header>

  <section class="hero-main">
    <div class="hero-art" role="img" aria-label="Painted illustration of a woman in a flowing spotted dress"></div>
    <div class="hero-copy">
      <h1>Restore your<br>natural comfort</h1>
      <p>Hormone-free moisturizer suppositories for<br>daily softness and lasting relief.</p>
      <span class="btn">Shop Suppositories</span>
    </div>
  </section>

  <section class="hero-offer">
    <p class="lead">First order deal,<br>just for you</p>
    <p class="pct">40%<br>off your kit</p>
    <div class="rule"></div>
    <p class="tag">USE CODE CORLANI40</p>
  </section>

  <section class="hero-photo">
    <div class="portrait" role="img" aria-label="Portrait photo of a smiling woman touching her cheeks"></div>
    <span class="badge">30%</span>
    <span class="heart"></span>
    <svg style="position:absolute;right:11px;top:326px" width="12" height="11" viewBox="0 0 12 11" fill="none" stroke="#3b3336" stroke-width="1.3"><path d="M6 10S1 6.8 1 3.6A2.5 2.5 0 0 1 6 2.6a2.5 2.5 0 0 1 5 1C11 6.8 6 10 6 10z"/></svg>
  </section>

  <div class="tabs">
    <div class="tab highlight">Product Section</div>
    <div class="tab highlight">How It Works</div>
    <div class="tab">Benefits</div>
    <div class="tab">Ingredients</div>
    <div class="tab">Directions</div>
    <div class="tab">Subscription</div>
  </div>

  <div class="divider"></div>

  <section class="products">
    <article class="card">
      <div class="shot" role="img" aria-label="Product photo of a suppository box"></div>
      <h3>Daily Moisture Ovules,<br>Fragrance-Free Set</h3>
      <a href="#">Shop now ➜</a>
    </article>
    <article class="card">
      <div class="shot" role="img" aria-label="Product photo of a single suppository"></div>
      <h3>Vitamin E Soothing<br>Suppositories</h3>
      <a href="#">Add to cart ➜</a>
    </article>
    <article class="card">
      <div class="shot" role="img" aria-label="Product photo of a starter kit with applicator"></div>
      <h3>Starter Kit with<br>Applicator &amp; Guide</h3>
      <a href="#">Add to cart ➜</a>
    </article>
    <article class="card">
      <div class="shot" role="img" aria-label="Product photo of a monthly supply box"></div>
      <h3>Aloe &amp; Coconut Blend,<br>Monthly Supply</h3>
      <a href="#">Shop now ➜</a>
    </article>
    <article class="card">
      <div class="shot" role="img" aria-label="Product photo of a night care pack"></div>
      <h3>Night Repair Ovules,<br>Subscribe &amp; Save Pack</h3>
      <a href="#">Subscribe ➜</a>
    </article>
  </section>
</body>
</html>
```